Velk Partners Building Business Cards

We need a business card that reflects our business as "Solar Experts" in San Diego. Browse our website www.velkpartners.example our License needs to be displayed as "CSLB# 3867140" our phone number is (619) 555-0187

Save thousands on your electric bills and increase the value of your home while helping to protect the environment. Our solar installation experts will help you design the system that's right for you, using only the highest quality equipment that will look great and give you ideal performance. Our goal is to make you energy independent, and get your electric bill to 0.

Paul Osterby
(619) 555-0187
paul@velkpartners.example

Target Market(s)

Home owners in san diego looking for solar

Industry/Entity Type

Solar Energy

Contact Information for Business Card

Paul Osterby
(619) 555-0187
paul@velkpartners.example

Font styles to use
Other font styles liked:
• Use our logo font

Requirements
Must have
• License needs to be displayed as "CSLB# 3867140" our phone number is (619) 555-0187
Nice to have
• Real images of rooftop home solar in san diego
Should not have
• our business address

```html
<!DOCTYPE html>
<html lang="en">
<head>
<meta charset="utf-8">
<title>Velk Partners Building – Business Card</title>
<link rel="stylesheet" href="https://fonts.googleapis.com/css2?family=PT+Sans:ital,wght@0,400;0,700;1,400&display=swap">
<style>
  :root {
    --navy: #1a3d73;
    --orange: #f7ab00;
    --ink: #555a60;
    --rule: #c9cbcf;
    --paper: #ffffff;
    --backdrop: #4b4b4d;
  }
  * { box-sizing: border-box; margin: 0; padding: 0; }
  html, body {
    width: 1105px; height: 1200px; overflow: hidden;
    background: var(--backdrop);
    font-family: "PT Sans", sans-serif;
  }
  .canvas { position: relative; width: 1105px; height: 1200px; }

  .card {
    position: absolute; left: 193px; width: 720px; height: 412px;
    box-shadow: 0 6px 14px rgba(0,0,0,.45);
  }
  .card-front { top: 167px; background: var(--paper); }
  .card-back { top: 623px; background: var(--navy); }

  .wordmark {
    position: absolute; left: 54px; top: 180px;
    font-size: 30px; font-weight: 700; color: var(--navy);
    letter-spacing: -0.3px; white-space: nowrap;
  }

  .divider {
    position: absolute; left: 384px; top: 109px;
    width: 1px; height: 200px; background: var(--rule);
  }

  .contact { position: absolute; left: 418px; top: 112px; }
  .contact-name {
    font-size: 26px; font-weight: 700; color: var(--navy); line-height: 32px;
  }
  .contact-title {
    font-size: 20px; color: var(--orange); line-height: 24px;
  }
  .contact-license {
    margin-top: 14px; font-size: 19px; color: var(--ink); line-height: 24px;
  }
  .contact-lines { list-style: none; margin-top: 14px; }
  .contact-lines li {
    display: flex; align-items: center; gap: 10px;
    font-size: 19px; color: var(--ink); line-height: 27px;
  }
  .contact-lines svg { width: 17px; height: 17px; flex: none; fill: var(--navy); }

  .accent-band { position: absolute; left: 0; bottom: 0; width: 720px; height: 28px; }

  .back-mark {
    position: absolute; left: 0; right: 0; top: 168px;
    display: flex; justify-content: center; align-items: center; gap: 16px;
  }
  .back-mark-dot { width: 38px; height: 38px; border-radius: 50%; background: var(--orange); }
  .back-mark-name { font-size: 36px; font-weight: 700; color: var(--paper); }

  .back-web {
    position: absolute; left: 0; right: 0; top: 336px;
    text-align: center; font-size: 19px; font-style: italic;
    letter-spacing: 4px; color: var(--paper);
  }
</style>
</head>
<body>
<div class="canvas">

  <section class="card card-front">
    <div class="wordmark">Velk Partners Building</div>
    <div class="divider"></div>

    <div class="contact">
      <div class="contact-name">Paul Osterby</div>
      <div class="contact-title">CEO/Founder</div>
      <div class="contact-license">CSLB# 3867140</div>
      <ul class="contact-lines">
        <li>
          <svg viewBox="0 0 16 16" aria-hidden="true"><path d="M3.6 1.2l2.2 2.6c.4.5.3 1.1-.1 1.5L4.6 6.4c.9 2 2.9 4 5 5l1.1-1.1c.4-.4 1-.5 1.5-.1l2.6 2.2c.5.4.5 1.1.1 1.6l-1.2 1.2c-.6.6-1.5.8-2.3.5C6.7 14.3 1.7 9.3.3 4.6 0 3.8.2 2.9.8 2.3L2 1.1c.5-.4 1.2-.4 1.6.1z"/></svg>
          <span>(619) 555-0187</span>
        </li>
        <li>
          <svg viewBox="0 0 16 16" aria-hidden="true"><path d="M1 3h14v1.2L8 8.6 1 4.2z"/><path d="M1 5.6l7 4.4 7-4.4V13H1z"/></svg>
          <span>paul@velkpartners.example</span>
        </li>
        <li>
          <svg viewBox="0 0 16 16" aria-hidden="true"><circle cx="8" cy="8" r="7.5"/><path d="M4 4.5c1.2.3 2 1 2.2 2 .2 1-.8 1.4-.5 2.4.3 1 1.6 1 1.6 2.3 0 .8-.4 1.6-.9 2.3M11 3c-.8.8-1 1.6-.4 2.3.6.7 1.8.5 2.2 1.5.3.8 0 1.6-.6 2.2" fill="none" stroke="#fff" stroke-width="1.1"/></svg>
          <span>www.velkpartners.example</span>
        </li>
      </ul>
    </div>

    <svg class="accent-band" viewBox="0 0 720 28" preserveAspectRatio="none" aria-hidden="true">
      <polygon points="0,0 469,0 461,28 0,28" fill="var(--navy)"/>
      <polygon points="475,0 720,0 720,28 467,28" fill="var(--orange)"/>
    </svg>
  </section>

  <section class="card card-back">
    <div class="back-mark">
      <span class="back-mark-dot"></span>
      <span class="back-mark-name">Velk Partners Building</span>
    </div>
    <div class="back-web">www.velkpartners.example</div>
  </section>

</div>
</body>
</html>
```